Poster design for Belgian waffles

We are a local frozen yogurt chain that will introduce a new product for winter. It is Belgian waffle. You can have it a plain, with toppings such fresh fruit or with our frozen yogurt. We need two posters, one for introduction of the product and one that has pricing on it.

Target Market(s)

College students and young professionals

Industry/Entity Type

Pricing

```html
<!DOCTYPE html>
<html lang="en">
<head>
<meta charset="utf-8">
<title>Belgian Waffle Poster</title>
<link rel="stylesheet" href="https://fonts.googleapis.com/css2?family=Roboto+Condensed:wght@700&family=Righteous&family=Open+Sans:wght@600;700&display=swap">
<style>
  :root {
    --page-bg: #ffffff;
    --poster-light: #eedcb4;
    --poster-mid: #e4c57f;
    --poster-deep: #d9b165;
    --maroon: #6d1010;
    --brand-red: #e8473a;
    --brand-green: #8aa43a;
    --bar-top: #f39a55;
    --bar-bottom: #d4591c;
    --bar-edge: #a9420f;
    --white: #ffffff;
    --waffle-light: #f7cf79;
    --waffle-deep: #d98d2c;
  }
  * { margin: 0; padding: 0; box-sizing: border-box; }
  html, body {
    width: 1200px;
    height: 1200px;
    overflow: hidden;
    background: var(--page-bg);
  }
  .poster {
    position: absolute;
    left: 240px;
    top: 38px;
    width: 718px;
    height: 1124px;
    overflow: hidden;
    background:
      radial-gradient(ellipse 70% 45% at 50% 58%, var(--poster-deep) 0%, rgba(217,177,101,0) 100%),
      linear-gradient(180deg, var(--poster-light) 0%, var(--poster-mid) 45%, var(--poster-mid) 75%, var(--poster-light) 100%);
  }
  .brand {
    position: absolute;
    top: 62px;
    left: 0;
    width: 100%;
    display: flex;
    justify-content: center;
    align-items: center;
    gap: 10px;
    font-family: "Open Sans", sans-serif;
    font-weight: 700;
    font-size: 42px;
    letter-spacing: 1px;
    color: var(--brand-red);
  }
  .brand-dot {
    width: 18px;
    height: 18px;
    border-radius: 50%;
    background: var(--brand-green);
  }
  .intro {
    position: absolute;
    top: 182px;
    left: 0;
    width: 100%;
    text-align: center;
    font-family: "Roboto Condensed", sans-serif;
    font-weight: 700;
    font-size: 54px;
    color: var(--maroon);
    letter-spacing: 0.5px;
  }
  .title-main {
    position: absolute;
    top: 318px;
    left: 70px;
    font-family: "Righteous", sans-serif;
    font-size: 150px;
    line-height: 1;
    color: var(--maroon);
  }
  .title-sub {
    position: absolute;
    top: 452px;
    left: 262px;
    font-family: "Righteous", sans-serif;
    font-size: 124px;
    line-height: 1;
    color: var(--maroon);
  }
  .product-photo {
    position: absolute;
    left: 126px;
    top: 622px;
    width: 468px;
    height: 300px;
    border-radius: 14px;
    background: radial-gradient(ellipse at 50% 45%, var(--waffle-light) 0%, var(--waffle-deep) 70%, rgba(217,141,44,0) 100%);
  }
  .tagline-bar {
    position: absolute;
    left: 26px;
    top: 1018px;
    width: 667px;
    height: 52px;
    border-radius: 12px;
    border: 2px solid var(--bar-edge);
    background: linear-gradient(180deg, var(--bar-top) 0%, var(--bar-bottom) 100%);
    display: flex;
    align-items: center;
    justify-content: center;
    font-family: "Open Sans", sans-serif;
    font-weight: 700;
    font-size: 29px;
    color: var(--white);
  }
</style>
</head>
<body>
  <main class="poster">
    <div class="brand"><span class="brand-name">yoglow</span><span class="brand-dot"></span></div>
    <h2 class="intro">INTRODUCING THE DELICIOUS</h2>
    <h1>
      <span class="title-main">Belgian</span>
      <span class="title-sub">Waffle</span>
    </h1>
    <div class="product-photo" role="img" aria-label="Photo of two golden square Belgian waffles stacked at an angle"></div>
    <div class="tagline-bar">Belgian Waffle from Yoglow</div>
  </main>
</body>
</html>
```